Software as a Service to manage Home Care Management

We need a web site designed for Home Care Management Software as a Service product, that facilitates Home Care organizations to manage and schedule carers to visit client homes. We want a modern look and feel using our existing logo.

Target Market(s)

Home Care Management organizations. Product is similar to: https://carelarkly.io/

Coding

Coded - Design and coding required

Number of Pages Required

3 page

```html
<!DOCTYPE html>
<html lang="en">
<head>
<meta charset="utf-8">
<title>Visitwell – Home Care Management Software</title>
<link rel="stylesheet" href="https://fonts.googleapis.com/css2?family=Cinzel:wght@400;500;600&family=Arimo:wght@400;500&family=Montserrat:wght@400;500&display=swap">
<style>
:root{
  --pink:#e9196f;
  --pink-dark:#d5166a;
  --ink:#2b2b2b;
  --muted:#666;
  --navy-1:#0c1b2c;
  --navy-2:#17304a;
  --footer:#222222;
  --white:#ffffff;
}
*{box-sizing:border-box;margin:0;padding:0}
html,body{width:1200px;height:4542px;overflow:hidden}
body{position:relative;font-family:"Arimo",Arial,sans-serif;color:var(--ink);background:var(--white)}
.serif{font-family:"Cinzel",Georgia,serif;text-transform:uppercase}
section,header,footer{position:absolute;left:0;width:1200px;overflow:hidden}
.abs{position:absolute}
.center{left:0;width:1200px;text-align:center}
.pink{color:var(--pink)}
.rule{position:absolute;left:576px;width:48px;height:2px;background:var(--pink)}
.btn-outline{position:absolute;display:flex;align-items:center;justify-content:center;border:1.5px solid var(--pink);color:var(--pink);font-family:"Cinzel",Georgia,serif;text-transform:uppercase;font-size:13px;letter-spacing:.5px;background:#fff}

/* header */
.site-header{top:0;height:122px;background:#fff}
.brand{display:flex;align-items:center;gap:10px}
.brand-dot{width:30px;height:30px;border-radius:50%;background:var(--pink)}
.brand-name{font-family:"Cinzel",Georgia,serif;text-transform:uppercase;font-size:22px;font-weight:500;color:#333;letter-spacing:.5px;white-space:nowrap}
.main-nav{position:absolute;top:54px}
.main-nav a{position:absolute;white-space:nowrap;transform:translateX(-50%);font-family:"Cinzel",Georgia,serif;text-transform:uppercase;font-size:13px;font-weight:500;color:#333;text-decoration:none}
.main-nav a.active{color:var(--pink)}

/* hero */
.hero{top:122px;height:704px;background:radial-gradient(ellipse at 60% 40%,#1f3e5a 0%,var(--navy-2) 35%,var(--navy-1) 80%)}
.hero-title{top:215px;font-size:76px;font-weight:500;color:#fff;letter-spacing:2px;line-height:1}
.hero-sub{font-size:18px;color:#fff;letter-spacing:1px}
.hero-btn{position:absolute;left:507px;top:429px;width:187px;height:55px;background:var(--pink);color:#fff;font-family:"Cinzel",Georgia,serif;text-transform:uppercase;font-size:18px;display:flex;align-items:center;justify-content:center}

/* welcome */
.welcome{top:826px;height:619px}
.section-title{font-family:"Cinzel",Georgia,serif;text-transform:uppercase;font-size:30px;font-weight:500;color:#333;letter-spacing:1px}
.welcome-text{position:absolute;left:250px;width:700px;top:142px;text-align:center;font-size:13.5px;line-height:28px;color:#555}
.audience{position:absolute;top:295px;width:280px;text-align:center}
.audience .ring{width:126px;height:126px;margin:0 auto;border-radius:50%;border:2px solid var(--pink);display:flex;align-items:center;justify-content:center}
.audience .ring.filled{background:var(--pink)}
.audience h3{margin-top:24px;font-family:"Cinzel",Georgia,serif;text-transform:uppercase;font-size:18px;font-weight:400;color:#333;letter-spacing:1px}
.audience p{margin-top:14px;font-size:13px;line-height:27px;color:#777}

/* software band */
.software{top:1445px;height:518px;background:linear-gradient(115deg,#e41a6f 0%,#e61e79 55%,#f0549b 100%)}
.phone{position:absolute;left:181px;top:61px;width:252px;height:520px;border:3px solid #d9d9d9;border-radius:38px;background:#f4f4f4}
.phone-screen{position:absolute;left:16px;top:72px;width:214px;height:460px;background:#fff;border:2px solid #222;display:flex;align-items:center;justify-content:center}
.software h2{position:absolute;left:525px;font-family:"Cinzel",Georgia,serif;text-transform:uppercase;color:#fff;font-weight:500;letter-spacing:1px;white-space:nowrap}
.feature-list{position:absolute;left:532px;top:196px;list-style:none}
.feature-list li{height:43px;display:flex;align-items:center;gap:16px;font-size:14.5px;color:#fff}
.software-btn{position:absolute;left:532px;top:424px;width:145px;height:46px;border:2px solid #fff;color:#fff;font-family:"Cinzel",Georgia,serif;text-transform:uppercase;font-size:15px;display:flex;align-items:center;justify-content:center}

/* numbers */
.numbers{top:1963px;height:765px}
.tile{position:absolute;width:324px;height:252px}
.photo{background:linear-gradient(135deg,#c9b4a6,#8d7868)}
.stat{text-align:center}
.stat .value{margin-top:50px;font-family:"Cinzel",Georgia,serif;font-size:32px;color:var(--pink)}
.stat .label{margin-top:8px;font-family:"Cinzel",Georgia,serif;text-transform:uppercase;font-size:14px;line-height:28px;color:#333;letter-spacing:.5px}
.stat .btn-outline{left:105px;top:160px;width:116px;height:41px}

/* banner */
.banner{top:2728px;height:532px;background:linear-gradient(90deg,#e9e9e7 0%,#e4e2dd 40%,#d7cbb9 70%,#e8d8b5 100%)}
.banner-photo{position:absolute;left:600px;top:0;width:600px;height:532px;background:radial-gradient(ellipse at 50% 55%,#d4bda4 0%,#cfc3b1 45%,rgba(228,226,221,0) 75%)}
.banner h3{position:absolute;left:111px;font-family:"Cinzel",Georgia,serif;text-transform:uppercase;font-weight:500;color:#333;letter-spacing:1px;white-space:nowrap}
.banner p{position:absolute;left:111px;top:240px;width:500px;font-size:13px;line-height:29px;color:#555}

/* blog */
.blog{top:3260px;height:592px}
.post{position:absolute;top:128px;width:313px}
.post-image{height:233px}
.post h4{margin-top:36px;font-family:"Cinzel",Georgia,serif;text-transform:uppercase;font-size:15px;font-weight:500;color:#333;letter-spacing:.5px}
.post time{display:block;margin-top:14px;font-family:"Cinzel",Georgia,serif;text-transform:uppercase;font-size:14px;color:var(--pink)}
.post p{margin-top:12px;font-size:13px;line-height:26px;color:#666}

/* newsletter */
.newsletter{top:3852px;height:310px;background:linear-gradient(115deg,#e41a6f 0%,#e61e79 55%,#f0549b 100%)}
.newsletter-form{position:absolute;left:247px;top:183px;width:706px;height:60px;display:flex}
.newsletter-form .field{flex:1;background:#fff;display:flex;align-items:center;padding-left:18px;font-size:13px;color:#555}
.newsletter-form .submit{width:107px;background:#222;color:#fff;font-family:"Cinzel",Georgia,serif;text-transform:uppercase;font-size:14px;display:flex;align-items:center;justify-content:center}

/* footer */
.site-footer{top:4162px;height:380px;background:var(--footer);color:#fff}
.footer-title{position:absolute;top:32px;font-family:"Cinzel",Georgia,serif;text-transform:uppercase;font-size:22px;font-weight:400;letter-spacing:1px}
.input{position:absolute;height:35px;background:#fff;color:#333;font-size:11px;display:flex;align-items:center;padding-left:12px}
.send{position:absolute;left:116px;top:232px;width:97px;height:32px;background:var(--pink);color:#fff;font-size:12px;display:flex;align-items:center;justify-content:center}
.contact-row{position:absolute;left:592px;display:flex;align-items:flex-start;gap:14px}
.icon-ring{width:42px;height:42px;border-radius:50%;border:1.5px solid #fff;display:flex;align-items:center;justify-content:center;flex:none}
.contact-row .label{font-family:"Montserrat",Arial,sans-serif;font-size:13px}
.contact-row .detail{font-family:"Montserrat",Arial,sans-serif;font-size:11.5px;line-height:19px;color:#ddd}
.social{position:absolute;top:176px;width:38px;height:38px;border-radius:50%;border:1.5px solid #fff}
.copyright{position:absolute;top:332px;left:0;width:1200px;text-align:center;font-family:"Montserrat",Arial,sans-serif;font-size:13px;color:#ddd}
</style>
</head>
<body>

<header class="site-header">
  <div class="brand abs" style="left:111px;top:46px">
    <span class="brand-dot"></span><span class="brand-name">Visitwell</span>
  </div>
  <nav class="main-nav" style="left:0">
    <a class="active" style="left:455px">Home</a>
    <a style="left:567px">About Us</a>
    <a style="left:687px">Service</a>
    <a style="left:807px">Product</a>
    <a style="left:916px">News</a>
    <a style="left:1038px">Contact Us</a>
  </nav>
</header>

<section class="hero" role="img" aria-label="Dark blue digital data background with glowing lines">
  <h1 class="abs center serif hero-title">Visitwell</h1>
  <p class="abs center serif hero-sub" style="top:337px">Sed ut perspiciatis unde omnis iste natus error sit</p>
  <p class="abs center serif hero-sub" style="top:379px">voluptatem accusantium doloremque</p>
  <a class="hero-btn">Read More</a>
</section>

<section class="welcome">
  <h2 class="abs center section-title" style="top:64px">Welcome to <span class="pink">Visitwell</span></h2>
  <span class="rule" style="top:119px"></span>
  <p class="welcome-text">Sed ut perspiciatis unde omnis iste natus error sit voluptatem accusantium doloremque laudantium, totam rem aperiam, eaque ipsa quae ab illo inventore veritatis et quasi architecto beatae vitae dicta sunt explicabo. Nemo enim ipsam voluptatem quia voluptas sit aspernatur aut odit aut fugit, sed quia consequuntur magni dolores eos et quasi qui ratione voluptatem sequi nesciunt.</p>

  <div class="audience" style="left:128px">
    <div class="ring">
      <svg width="62" height="62" viewBox="0 0 62 62" fill="none" stroke="#333" stroke-width="2">
        <circle cx="31" cy="8" r="5"/><rect x="24" y="15" width="14" height="8" rx="3"/>
        <path d="M31 23v6M12 29h38M12 29v4M31 29v4M50 29v4"/>
        <circle cx="12" cy="38" r="4"/><circle cx="31" cy="38" r="4"/><circle cx="50" cy="38" r="4"/>
        <rect x="6" y="44" width="12" height="7" rx="3"/><rect x="25" y="44" width="12" height="7" rx="3"/><rect x="44" y="44" width="12" height="7" rx="3"/>
        <path d="M4 56h54"/>
      </svg>
    </div>
    <h3>For Managers</h3>
    <p>Sed ut perspiciatis unde omnis iste natus error sit voluptatem accusantium dolom am rem aperiam, eaque ipsa</p>
  </div>
  <div class="audience" style="left:459px">
    <div class="ring filled">
      <svg width="64" height="64" viewBox="0 0 64 64" fill="none" stroke="#fff" stroke-width="2">
        <rect x="8" y="10" width="34" height="44" rx="3"/><rect x="18" y="6" width="14" height="8" rx="2"/>
        <path d="M14 24l3 3 5-5M26 25h10M14 36l3 3 5-5M26 37h6M14 47h10"/>
        <circle cx="44" cy="44" r="13"/><path d="M44 37v7l5 3"/>
      </svg>
    </div>
    <h3>For Carers</h3>
    <p>Sed ut perspiciatis unde omnis iste natus error sit voluptatem accusantium dolom am rem aperiam, eaque ipsa</p>
  </div>
  <div class="audience" style="left:790px">
    <div class="ring">
      <svg width="64" height="64" viewBox="0 0 64 64" fill="none" stroke="#333" stroke-width="2">
        <circle cx="20" cy="10" r="5"/><path d="M13 20h14v16h-3v20h-8V36h-3z"/>
        <circle cx="44" cy="10" r="5"/><path d="M37 20h14l3 18h-5v18h-8V38h-5z"/>
        <circle cx="32" cy="30" r="3.5"/><path d="M28 37h8v10h-2v9h-4v-9h-2z"/>
      </svg>
    </div>
    <h3>For Families</h3>
    <p>Sed ut perspiciatis unde omnis iste natus error sit voluptatem accusantium dolom am rem aperiam, eaque ipsa</p>
  </div>
</section>

<section class="software">
  <div class="phone">
    <svg class="abs" style="left:100px;top:18px" width="50" height="36" viewBox="0 0 50 36"><circle cx="25" cy="8" r="5" fill="#222"/><rect x="13" y="26" width="26" height="4" rx="2" fill="#222"/><circle cx="5" cy="28" r="2" fill="#222"/></svg>
    <div class="phone-screen">
      <div class="brand"><span class="brand-dot" style="width:22px;height:22px"></span><span class="brand-name" style="font-size:18px">Visitwell</span></div>
    </div>
  </div>
  <h2 style="top:72px;font-size:40px">Optimised Home</h2>
  <h2 style="top:122px;font-size:29px">Care Software</h2>
  <ul class="feature-list">
    <li><svg width="15" height="15" viewBox="0 0 16 16"><circle cx="8" cy="8" r="7" fill="none" stroke="#fff" stroke-width="1.6"/><path d="M4.8 8.2l2.2 2.2 4.2-4.4" fill="none" stroke="#fff" stroke-width="1.6"/></svg>Sed ut perspiciatis unde omnis iste natus</li>
    <li><svg width="15" height="15" viewBox="0 0 16 16"><circle cx="8" cy="8" r="7" fill="none" stroke="#fff" stroke-width="1.6"/><path d="M4.8 8.2l2.2 2.2 4.2-4.4" fill="none" stroke="#fff" stroke-width="1.6"/></svg>Error sit voluptatem accusantium doloremque</li>
    <li><svg width="15" height="15" viewBox="0 0 16 16"><circle cx="8" cy="8" r="7" fill="none" stroke="#fff" stroke-width="1.6"/><path d="M4.8 8.2l2.2 2.2 4.2-4.4" fill="none" stroke="#fff" stroke-width="1.6"/></svg>Laudantium, totam rem aperiam, eaque</li>
    <li><svg width="15" height="15" viewBox="0 0 16 16"><circle cx="8" cy="8" r="7" fill="none" stroke="#fff" stroke-width="1.6"/><path d="M4.8 8.2l2.2 2.2 4.2-4.4" fill="none" stroke="#fff" stroke-width="1.6"/></svg>Ipsa quae ab illo inventore veritatis et quasi</li>
    <li><svg width="15" height="15" viewBox="0 0 16 16"><circle cx="8" cy="8" r="7" fill="none" stroke="#fff" stroke-width="1.6"/><path d="M4.8 8.2l2.2 2.2 4.2-4.4" fill="none" stroke="#fff" stroke-width="1.6"/></svg>Architecto beatae vitae dicta sunt explicabo</li>
  </ul>
  <a class="software-btn">Read More</a>
</section>

<section class="numbers">
  <h2 class="abs center section-title" style="top:74px">Success <span class="pink">in Numbers</span></h2>
  <span class="rule" style="top:129px"></span>

  <div class="tile photo" style="left:111px;top:188px" role="img" aria-label="Smiling elderly couple portrait"></div>
  <div class="tile stat" style="left:437px;top:188px">
    <div class="value">96%</div>
    <div class="label">Sed ut perspiciatis unde<br>omnis iste natus</div>
    <a class="btn-outline">Read More</a>
  </div>
  <div class="tile photo" style="left:765px;top:188px;background:linear-gradient(135deg,#e8e2da,#b9a99a)" role="img" aria-label="Elderly couple looking at a laptop together"></div>

  <div class="tile stat" style="left:111px;top:442px">
    <div class="value">25M</div>
    <div class="label">Sed ut perspiciatis unde<br>omnis iste natus</div>
    <a class="btn-outline">Read More</a>
  </div>
  <div class="tile photo" style="left:437px;top:442px;background:radial-gradient(circle at 50% 50%,#e6e3dc,#8f8a80)" role="img" aria-label="Group of seniors in a circle seen from below"></div>
  <div class="tile stat" style="left:765px;top:442px">
    <div class="value">15K</div>
    <div class="label">Sed ut perspiciatis unde<br>omnis iste natus</div>
    <a class="btn-outline">Read More</a>
  </div>
</section>

<section class="banner">
  <div class="banner-photo" role="img" aria-label="Happy senior couple embracing outdoors in sunlight"></div>
  <h3 style="top:128px;font-size:28px">Sed ut perspiciatis</h3>
  <h3 style="top:172px;font-size:36px">Unde omnis iste natus</h3>
  <p>Nemo enim ipsam voluptatem quia voluptas sit aspernatur aut odit aut fugit, sed quia consequuntur magni dolores eos qui ratione voluptatem sequi nesciunt. quisquam est, qui dolorem ipsum quia dolor sit amet</p>
  <a class="btn-outline" style="left:111px;top:354px;width:144px;height:49px;font-size:15px;background:transparent">Read More</a>
</section>

<section class="blog">
  <h2 class="abs center section-title" style="top:44px">Latest <span class="pink">Blog</span></h2>
  <span class="rule" style="top:99px"></span>

  <article class="post" style="left:111px">
    <div class="post-image" style="background:linear-gradient(135deg,#1d4f86,#5c8fc6)" role="img" aria-label="Hands on a laptop with digital charts"></div>
    <h4>Sed ut perspiciatis unde</h4>
    <time>30 November 2020</time>
    <p>Nemo enim ipsam voluptatem quia voluptas sit as pernatur aut odit aut fugit, sed quia consequuntur magni dolores eos qui ratione</p>
  </article>
  <article class="post" style="left:444px">
    <div class="post-image" style="background:linear-gradient(135deg,#cdb99d,#8f6e4e)" role="img" aria-label="Person reviewing paperwork at a desk"></div>
    <h4>Sed ut perspiciatis unde</h4>
    <time>30 November 2020</time>
    <p>Nemo enim ipsam voluptatem quia voluptas sit as pernatur aut odit aut fugit, sed quia consequuntur magni dolores eos qui ratione</p>
  </article>
  <article class="post" style="left:777px">
    <div class="post-image" style="background:linear-gradient(135deg,#f1ece9,#c9c4cc)" role="img" aria-label="Hand holding a phone in front of a report on a laptop"></div>
    <h4>Sed ut perspiciatis unde</h4>
    <time>30 November 2020</time>
    <p>Nemo enim ipsam voluptatem quia voluptas sit as pernatur aut odit aut fugit, sed quia consequuntur magni dolores eos qui ratione</p>
  </article>
</section>

<section class="newsletter">
  <h2 class="abs center serif" style="top:64px;font-size:32px;font-weight:400;color:#fff;letter-spacing:1px">Our Newsletter</h2>
  <span class="rule" style="top:117px;background:#fff"></span>
  <p class="abs center" style="top:135px;font-size:15px;color:#fff">Sed ut perspiciatis unde omnis iste natus error sit voluptatem</p>
  <div class="newsletter-form">
    <div class="field">Enter Email :</div>
    <div class="submit">Signup</div>
  </div>
</section>

<footer class="site-footer">
  <h3 class="footer-title" style="left:116px">Contact Us</h3>
  <div class="input" style="left:116px;top:90px;width:182px">First Name :</div>
  <div class="input" style="left:310px;top:90px;width:176px">Last Name :</div>
  <div class="input" style="left:116px;top:134px;width:182px">Company Name :</div>
  <div class="input" style="left:310px;top:134px;width:176px">Email address :</div>
  <div class="input" style="left:116px;top:180px;width:370px">Comment :</div>
  <div class="send">SUBMIT</div>

  <h3 class="footer-title" style="left:599px">Address</h3>
  <div class="contact-row" style="top:100px">
    <span class="icon-ring"><svg width="16" height="18" viewBox="0 0 16 18"><path d="M8 1a6 6 0 0 0-6 6c0 4.5 6 10 6 10s6-5.5 6-10a6 6 0 0 0-6-6z" fill="none" stroke="#fff" stroke-width="1.6"/><circle cx="8" cy="7" r="2" fill="#fff"/></svg></span>
    <div><div class="label">ADDRESS</div><div class="detail">25-26 Lorem Ipsum Dummy<br>Lorem Ipsum</div></div>
  </div>
  <div class="contact-row" style="top:166px">
    <span class="icon-ring"><svg width="16" height="16" viewBox="0 0 16 16"><path d="M3 1.5l3 .5 1 3-2 1.5a9 9 0 0 0 4.5 4.5L11 9l3 1 .5 3-2 1.5C6.5 14 1.5 9 1.5 3.5z" fill="#fff"/></svg></span>
    <div><div class="label">PHONE NUMBER</div><div class="detail">000-555-0142</div></div>
  </div>
  <div class="contact-row" style="top:229px">
    <span class="icon-ring"><svg width="18" height="13" viewBox="0 0 18 13"><rect x="1" y="1" width="16" height="11" rx="1" fill="#fff"/><path d="M1.5 1.5L9 7.5l7.5-6" fill="none" stroke="#222" stroke-width="1.4"/></svg></span>
    <div><div class="label">EMAIL US</div><div class="detail">info@visitwell.io</div></div>
  </div>

  <div class="brand abs" style="left:858px;top:120px">
    <span class="brand-dot" style="width:26px;height:26px"></span><span class="brand-name" style="color:#fff;font-size:20px">Visitwell</span>
  </div>
  <span class="social" style="left:906px"></span>
  <span class="social" style="left:948px"></span>
  <span class="social" style="left:992px"></span>

  <p class="copyright">©2020 Visitwell. All rights reserved.</p>
</footer>

</body>
</html>
```